Maple Roster Business Card for recruitment company

We are looking for a Business Card Design that incorporates our personal details and our busines name and logo. We are a specialized search consultancy that recruit Property and Construction professionals.
We would like a business card that stands out and is appealing to the Construction and Property industry as well.

Target Market(s)

people in the construction and property industry

Contact Information for Business Card

Business Name and logo

Font styles to use
Serif

Colors
0094D4
00A9DD
6FCCEA
C7EBF8
E9F6FB

Requirements
Must have
• Business name and logo as well as contact details
Should not have
• No photos of us please

```html
<!DOCTYPE html>
<html lang="en">
<head>
<meta charset="utf-8">
<title>Maple Roster – Business Card</title>
<link rel="stylesheet" href="https://fonts.googleapis.com/css2?family=Josefin+Sans:wght@400&family=Montserrat:wght@400;600;700;800&display=swap">
<style>
  :root {
    --canvas: #f1f1f1;
    --teal: #033d50;
    --paper: #ffffff;
    --mist: #8ba7b3;
    --ink: #1c1c1c;
    --white: #ffffff;
    --mark-faint: #ececec;
    --mark-grey: #cfcfcf;
  }
  * { box-sizing: border-box; margin: 0; padding: 0; }
  html, body { width: 800px; height: 1200px; overflow: hidden; }
  body {
    background: var(--canvas);
    position: relative;
    font-family: "Montserrat", sans-serif;
  }
  .card {
    position: absolute;
    left: 50px;
    width: 700px;
    height: 400px;
    overflow: hidden;
    background: var(--teal);
    box-shadow: 0 10px 28px rgba(0,0,0,0.16);
  }
  .card--front { top: 150px; }
  .card--back { top: 650px; }
  .card__shapes { position: absolute; inset: 0; width: 100%; height: 100%; }

  .brand-mark {
    position: absolute;
    border-radius: 50%;
  }
  .card--front .brand-mark {
    left: 478px;
    top: 252px;
    width: 192px;
    height: 192px;
    background: var(--mark-faint);
  }
  .card--back .brand-mark {
    left: 428px;
    top: 62px;
    width: 290px;
    height: 290px;
    background: var(--mark-grey);
    opacity: 0.55;
  }

  .wordmark {
    position: absolute;
    display: flex;
    align-items: center;
    gap: 12px;
    font-family: "Josefin Sans", sans-serif;
    font-weight: 400;
    letter-spacing: 0.01em;
    white-space: nowrap;
    line-height: 1;
  }
  .wordmark__dot {
    flex: none;
    border-radius: 50%;
    background: currentColor;
  }
  .card--front .wordmark {
    left: 399px;
    top: 189px;
    transform: translate(-50%, -50%);
    font-size: 54px;
    color: var(--teal);
  }
  .card--front .wordmark__dot { width: 14px; height: 14px; }
  .card--front .website {
    position: absolute;
    left: 385px;
    top: 318px;
    transform: translate(-50%, -50%);
    font-size: 19px;
    font-weight: 700;
    letter-spacing: 0.25em;
    color: var(--ink);
    white-space: nowrap;
  }

  .card--back .wordmark {
    left: 44px;
    top: 98px;
    font-size: 36px;
    gap: 9px;
    color: var(--white);
  }
  .card--back .wordmark__dot { width: 10px; height: 10px; }
  .holder__name {
    position: absolute;
    left: 44px;
    top: 166px;
    font-size: 27px;
    font-weight: 800;
    letter-spacing: 0.04em;
    color: var(--mist);
    white-space: nowrap;
  }
  .holder__role {
    position: absolute;
    left: 44px;
    top: 199px;
    font-size: 14px;
    color: var(--white);
    white-space: nowrap;
  }
  .contacts {
    position: absolute;
    left: 44px;
    top: 238px;
    list-style: none;
  }
  .contacts__item {
    display: flex;
    align-items: center;
    height: 24px;
    margin-bottom: 13px;
    font-size: 17px;
    font-weight: 600;
    color: var(--white);
    white-space: nowrap;
  }
  .contacts__icon { width: 20px; height: 20px; margin-right: 12px; flex: none; }
</style>
</head>
<body>

  <section class="card card--front" aria-label="Card front">
    <svg class="card__shapes" viewBox="0 0 870 497" preserveAspectRatio="none" aria-hidden="true">
      <defs>
        <linearGradient id="frontSweep" x1="0" y1="0" x2="0" y2="1">
          <stop offset="0.3" stop-color="#033d50"/>
          <stop offset="1" stop-color="#8ba7b3"/>
        </linearGradient>
      </defs>
      <ellipse cx="612" cy="300" rx="507" ry="382" fill="url(#frontSweep)"/>
      <ellipse cx="646" cy="268" rx="512" ry="388" fill="#033d50"/>
      <ellipse cx="640" cy="250" rx="507" ry="382" fill="#ffffff"/>
    </svg>
    <div class="brand-mark" role="img" aria-label="Faint brand mark decoration"></div>
    <h1 class="wordmark"><span class="wordmark__dot" aria-hidden="true"></span>MAPLE ROSTER</h1>
    <p class="website">www.mapleroster.nz</p>
  </section>

  <section class="card card--back" aria-label="Card back">
    <svg class="card__shapes" viewBox="0 0 870 497" preserveAspectRatio="none" aria-hidden="true">
      <defs>
        <linearGradient id="backSweep" x1="0" y1="0" x2="0" y2="1">
          <stop offset="0.35" stop-color="#033d50"/>
          <stop offset="1" stop-color="#8ba7b3"/>
        </linearGradient>
      </defs>
      <ellipse cx="975" cy="295" rx="533" ry="308" fill="url(#backSweep)"/>
      <ellipse cx="1006" cy="272" rx="538" ry="312" fill="#033d50"/>
      <ellipse cx="1000" cy="255" rx="533" ry="308" fill="#ffffff"/>
    </svg>
    <div class="brand-mark" role="img" aria-label="Large brand mark decoration"></div>

    <h2 class="wordmark"><span class="wordmark__dot" aria-hidden="true"></span>MAPLE ROSTER</h2>
    <p class="holder__name">CLARA BENTON</p>
    <p class="holder__role">Director | Senior Search Consultant</p>

    <ul class="contacts">
      <li class="contacts__item">
        <svg class="contacts__icon" viewBox="0 0 20 20" aria-hidden="true">
          <path d="M1 2h18v15l-9-2-9 2z" fill="#8ba7b3"/>
          <path d="M7 5c-1 0-1.5 1-1 2.5 1 2.5 3 4.5 5.5 5 1.2.3 2-.3 2-1l-1.6-1.3-1.2.8c-1-.5-2-1.5-2.4-2.5l.8-1.1L7.9 5z" fill="#ffffff"/>
        </svg>
        +64 27 555 0142
      </li>
      <li class="contacts__item">
        <svg class="contacts__icon" viewBox="0 0 20 20" aria-hidden="true">
          <path d="M1 2h18v15l-9-2-9 2z" fill="#8ba7b3"/>
          <rect x="5" y="6" width="10" height="7" fill="none" stroke="#ffffff" stroke-width="1.2"/>
          <path d="M5 6l5 4 5-4M5 13l4-3.5M15 13l-4-3.5" fill="none" stroke="#ffffff" stroke-width="1.1"/>
        </svg>
        clara@mapleroster.nz
      </li>
      <li class="contacts__item">
        <svg class="contacts__icon" viewBox="0 0 20 20" aria-hidden="true">
          <path d="M1 2h18v15l-9-2-9 2z" fill="#8ba7b3"/>
          <circle cx="10" cy="9.5" r="4.5" fill="none" stroke="#ffffff" stroke-width="1.1"/>
          <path d="M5.5 9.5h9M10 5v9M7.8 5.6c-1.2 2.4-1.2 5.4 0 7.8M12.2 5.6c1.2 2.4 1.2 5.4 0 7.8" fill="none" stroke="#ffffff" stroke-width="0.9"/>
        </svg>
        www.mapleroster.nz
      </li>
    </ul>
  </section>

</body>
</html>
```